Website for new child psychology practice

New clinical psychology practice in NSW Australia, specialising in work with children, adolescents and families. I would like to feature the colours in the logo, which was recently designed by pixelharbor designer Odette.
I am seeking a professional looking page, which is easy to navigate and is colourful and playful but not childish.
Target Market(s)
Parents and professionals
Industry/Entity Type
Health
Coding
Coded - Design and coding required
Number of Pages Required
1 page
Font styles to use
Serif
Requirements
Must have
- Pages for 'About us' 'Services' 'Fees and information' 'Contact us'
Should not have
- Childish stock photos

```html
<!DOCTYPE html>
<html lang="en">
<head>
<meta charset="utf-8">
<title>Dr Clara Hayes — Clinical Psychologist</title>
<link rel="stylesheet" href="https://fonts.googleapis.com/css2?family=Crimson+Pro:wght@600;700&family=Lato:wght@400;700&family=Open+Sans:wght@400&display=swap">
<style>
:root{
  --plum:#6b0a57;
  --coral:#e35a4f;
  --orange:#e8803f;
  --blush:#fdf2f8;
  --ink:#1c1c1c;
  --text:#3a3a3a;
  --white:#fff;
  --footer:#000;
}
*{margin:0;padding:0;box-sizing:border-box}
html,body{width:1200px;height:2803px;overflow:hidden}
body{position:relative;background:var(--white);font-family:'Lato',sans-serif;color:var(--text)}
.abs{position:absolute}
.serif{font-family:'Crimson Pro',serif;font-weight:700}

/* header */
.brand{display:flex;align-items:center;gap:10px}
.brand-dot{width:30px;height:30px;border-radius:50%;background:var(--plum)}
.brand-name{font-family:'Crimson Pro',serif;font-weight:700;font-size:28px;letter-spacing:.5px;color:var(--plum)}
.top-contact{top:32px;font-size:15px;color:var(--plum);display:flex;align-items:center;gap:8px}
.top-contact svg{width:14px;height:14px;fill:var(--plum)}
.sep{left:687px;top:32px;width:1px;height:20px;background:var(--plum)}

.btn{position:absolute;display:flex;align-items:center;justify-content:center;font-family:'Crimson Pro',serif;font-weight:700;font-size:16px;letter-spacing:.5px;border-radius:22px 0 0 22px;overflow:hidden}
.btn::after{content:"";position:absolute;right:-12px;top:-12px;width:32px;height:32px;border-radius:50%;background:var(--coral)}
.btn-plum{background:var(--plum);color:var(--white)}
.btn-white{background:var(--white);color:var(--coral)}
.btn-white.alt::after{background:var(--plum)}
.btn-quote{border-radius:24px 0 0 24px}

.nav{left:171px;top:88px;width:858px;height:64px;background:var(--orange);border-radius:10px 10px 0 0;display:flex;align-items:center;padding-left:55px;z-index:2}
.nav a{font-family:'Crimson Pro',serif;font-weight:700;font-size:16px;color:var(--white);text-decoration:none;letter-spacing:.4px}
.nav .search{width:26px;height:26px;border-radius:50%;background:var(--white);display:flex;align-items:center;justify-content:center}

/* hero */
.hero{left:0;top:118px;width:1200px;height:552px;background:linear-gradient(90deg,#6d0a5a 0%,#8a2477 30%,#b98aa8 48%,#d8cfc8 62%,#8c7a6b 100%)}
.hero-kicker{left:112px;top:260px;font-size:21px;color:var(--white)}
.hero-title{left:112px;top:300px;font-size:47px;color:var(--white);letter-spacing:.5px}
.hero-copy{left:112px;top:372px;width:380px;font-size:15.5px;line-height:29px;color:var(--white)}

/* about */
.about-ring{left:148px;top:779px;width:340px;height:340px;border-radius:50% 0 50% 50%;background:var(--coral)}
.about-img{left:140px;top:771px;width:340px;height:340px;border-radius:50% 0 50% 50%;background:linear-gradient(180deg,#6a5a8c 0%,#3c3b5e 45%,#8a6a72 65%,#2f6aa3 85%,#205385 100%)}
.sec-title{display:flex;align-items:center;gap:20px;font-size:35px;color:var(--ink);letter-spacing:.3px}
.sec-title .dot{width:22px;height:22px;border-radius:50%;background:var(--coral)}
.sec-title em{font-style:normal;color:var(--coral)}
.about-copy{left:569px;top:856px;width:513px;font-size:15px;line-height:25.7px;text-align:justify}

/* services */
.services{left:0;top:1198px;width:1200px;height:747px;background:var(--blush)}
.card{top:1360px;width:281px;height:485px;background:var(--white);border-radius:141px;overflow:hidden;text-align:center}
.card-img{margin:18px auto 0;width:218px;height:218px;border-radius:50%}
.card h3{margin:22px auto 0;width:190px;font-family:'Crimson Pro',serif;font-weight:700;font-size:20px;line-height:30px;color:var(--ink)}
.card p{margin:8px auto 0;width:245px;font-size:13.5px;line-height:26.5px;color:var(--text)}
.card-go{position:absolute;left:76px;bottom:0;width:128px;height:50px;background:var(--plum);border-radius:64px 64px 0 0;display:flex;justify-content:center;padding-top:13px}
.card-go span{width:22px;height:22px;border-radius:50%;background:var(--white);display:flex;align-items:center;justify-content:center}

/* fees */
.fees{left:0;top:1945px;width:1200px;height:421px;background:linear-gradient(90deg,#e25a50 0%,#e25a50 35%,#d9756c 55%,#b78384 72%,#6f7591 100%)}
.fees-title{left:112px;top:1995px;font-size:35px;color:var(--white);display:flex;align-items:center;gap:24px}
.fees-title .dot{width:24px;height:24px;border-radius:50%;background:var(--white)}
.fees-copy{left:112px;top:2060px;width:620px;font-family:'Open Sans',sans-serif;font-size:17.5px;line-height:34.5px;color:var(--white)}
.fees-copy p+p{margin-top:34px}

/* footer */
.footer{left:0;top:2366px;width:1200px;height:437px;background:var(--footer)}
.foot-brand .brand-name{color:var(--white);font-size:27px}
.foot-brand .brand-dot{background:var(--coral)}
.social{top:2542px;width:32px;height:32px;border-radius:50%;background:var(--white);display:flex;align-items:center;justify-content:center}
.social svg{width:16px;height:16px}
.foot-head{top:2460px;font-family:'Crimson Pro',serif;font-weight:700;font-size:20px;color:var(--white);letter-spacing:.3px}
.foot-list{top:2502px;list-style:none}
.foot-list li{display:flex;align-items:center;gap:10px;font-size:15.5px;color:var(--white);height:34.3px}
.foot-list svg{width:14px;height:12px;fill:var(--white)}
.contact-row{left:880px;display:flex;align-items:center;gap:12px;font-size:15.5px;line-height:27px;color:var(--white)}
.contact-row .ico{width:32px;height:32px;border-radius:50%;background:var(--white);display:flex;align-items:center;justify-content:center;flex:none}
.contact-row .ico svg{width:16px;height:16px;fill:#000}
.rule{left:112px;top:2709px;width:977px;height:1px;background:#8a8a8a}
.copyright{left:0;top:2742px;width:1200px;text-align:center;font-size:15.5px;font-weight:700;color:var(--white)}
</style>
</head>
<body>

<!-- header -->
<div class="abs brand" style="left:113px;top:26px">
  <span class="brand-dot"></span><span class="brand-name">DR CLARA HAYES</span>
</div>
<div class="abs top-contact" style="left:530px">
  <svg viewBox="0 0 24 24"><path d="M6.6 10.8a15.1 15.1 0 0 0 6.6 6.6l2.2-2.2a1 1 0 0 1 1-.25 11.4 11.4 0 0 0 3.6.57 1 1 0 0 1 1 1V20a1 1 0 0 1-1 1A17 17 0 0 1 3 4a1 1 0 0 1 1-1h3.5a1 1 0 0 1 1 1c0 1.250.2 2.450.57 3.570a1 1 0 0 1-.25 1z"/></svg>
  <span class="serif" style="font-size:15px">+1 555 014 2277</span>
</div>
<div class="abs sep"></div>
<div class="abs top-contact" style="left:717px">
  <svg viewBox="0 0 24 24"><path d="M2 5h20v14H2V5zm2 2v.4l8 5 8-5V7H4z"/></svg>
  <span>info@drclarahayes.com</span>
</div>
<div class="btn btn-plum btn-quote" style="left:940px;top:21px;width:175px;height:45px;font-size:15px">REQUEST A QUOTE</div>

<nav class="abs nav">
  <a href="#" style="margin-right:80px">HOME</a>
  <a href="#" style="margin-right:78px">ABOUT US</a>
  <a href="#" style="margin-right:78px">FEES AND INFORMATION</a>
  <a href="#" style="margin-right:68px">CONTACT US</a>
  <span class="search"><svg width="12" height="12" viewBox="0 0 24 24"><circle cx="10" cy="10" r="6" fill="none" stroke="#000" stroke-width="3"/><path d="M15 15l6 6" stroke="#000" stroke-width="3"/></svg></span>
</nav>

<!-- hero -->
<section class="abs hero" role="img" aria-label="Psychologist holding a folder in a bright office, purple wash on the left"></section>
<div class="abs hero-kicker serif">WELCOME TO</div>
<h1 class="abs hero-title serif">DR.CLARA HAYES</h1>
<p class="abs hero-copy">Lorem ipsum dolor sit amet, consectetur adipiscing elit, sed do eiusmod tempor incididunt ut labore et dolore magna aliqua.</p>
<div class="btn btn-white" style="left:113px;top:482px;width:175px;height:45px">GET STARTED</div>

<!-- about -->
<div class="abs about-ring"></div>
<div class="abs about-img" role="img" aria-label="Harbour city skyline at dusk"></div>
<h2 class="abs sec-title serif" style="left:569px;top:800px"><span class="dot"></span><span>ABOUT <em>DR.CLARA HAYES</em></span></h2>
<p class="abs about-copy">Lorem ipsum dolor sit amet, consectetur adipiscing elit, sed do eiusmod tempor incididunt ut labore et dolore magna aliqua. Ut enim ad minim veniam, quis nostrud exercitation ullamco laboris nisi ut aliquip ex ea commodo consequat. Duis aute irure dolor in reprehenderit in voluptate velit esse cillum dolore eu fugiat nulla pariatur. Excepteur sint occaecat cupidatat non proident, sunt in culpa qui officia deserunt mollit anim id est laborum.</p>
<div class="btn btn-plum" style="left:570px;top:1033px;width:175px;height:45px">READ MORE</div>

<!-- services -->
<section class="abs services"></section>
<h2 class="abs sec-title serif" style="left:0;top:1278px;width:1200px;justify-content:center"><span class="dot"></span><span>OUR <em>SERVICES</em></span></h2>

<article class="abs card" style="left:112px">
  <div class="card-img" role="img" aria-label="Open hands holding a calming object" style="background:linear-gradient(160deg,#e3c7b4 0%,#d4a88a 50%,#a8735a 100%)"></div>
  <h3>Lorem ipsum dolor sit ame</h3>
  <p>Lorem ipsum dolor sit amet, consectetur adipiscing elit, sed do eiusmod tempor incididunt ut labore et dolore magna aliqua.</p>
  <div class="card-go"><span><svg width="10" height="10" viewBox="0 0 10 10"><path d="M3 1l4 4-4 4" fill="none" stroke="#6b0a57" stroke-width="2"/></svg></span></div>
</article>

<article class="abs card" style="left:460px">
  <div class="card-img" role="img" aria-label="Therapist taking notes on a clipboard during a session" style="background:linear-gradient(135deg,#e8d6d2 0%,#d9c4c0 45%,#c97a74 70%,#3a3f58 100%)"></div>
  <h3>Sed do eiusmod tempor incididunt</h3>
  <p>Ut enim ad minim veniam, quis nostrud exercitation ullamco laboris nisi ut aliquip ex ea commodo consequat.</p>
  <div class="card-go"><span><svg width="10" height="10" viewBox="0 0 10 10"><path d="M3 1l4 4-4 4" fill="none" stroke="#6b0a57" stroke-width="2"/></svg></span></div>
</article>

<article class="abs card" style="left:808px">
  <div class="card-img" role="img" aria-label="Two women talking together in a calm setting" style="background:linear-gradient(120deg,#3e3a2e 0%,#7a6048 45%,#a8825e 65%,#5c4a3c 100%)"></div>
  <h3>Labore et dolore magna aliqua</h3>
  <p>Duis aute irure dolor in reprehenderit in voluptate velit esse cillum dolore eu voluptate velit esse cillum dolore fugiat nulla pariatur.</p>
  <div class="card-go"><span><svg width="10" height="10" viewBox="0 0 10 10"><path d="M3 1l4 4-4 4" fill="none" stroke="#6b0a57" stroke-width="2"/></svg></span></div>
</article>

<!-- fees -->
<section class="abs fees" role="img" aria-label="River city skyline and bridge at sunset, coral wash on the left"></section>
<h2 class="abs fees-title serif"><span class="dot"></span><span>FEES AND INFORMATION</span></h2>
<div class="abs fees-copy">
  <p>Lorem ipsum dolor sit amet, consectetur adipiscing elit, sed do eiusmod tempor incididunt ut labore et dolore magna aliqua.</p>
  <p>Ut enim ad minim veniam, quis nostrud exercitation ullamco laboris nisi ut aliquip ex ea commodo consequat.</p>
</div>
<div class="btn btn-white alt" style="left:113px;top:2255px;width:175px;height:45px">READ MORE</div>

<!-- footer -->
<footer class="abs footer"></footer>
<div class="abs brand foot-brand" style="left:118px;top:2473px">
  <span class="brand-dot"></span><span class="brand-name">DR CLARA HAYES</span>
</div>
<a class="abs social" style="left:111px" aria-label="Social profile"><svg viewBox="0 0 24 24"><path d="M10 14l4-4M8.5 11.5l-2 2a3 3 0 0 0 4 4l2-2M15.5 12.5l2-2a3 3 0 0 0-4-4l-2 2" fill="none" stroke="#000" stroke-width="2.2" stroke-linecap="round"/></svg></a>
<a class="abs social" style="left:169px" aria-label="Social profile"><svg viewBox="0 0 24 24"><path d="M10 14l4-4M8.5 11.5l-2 2a3 3 0 0 0 4 4l2-2M15.5 12.5l2-2a3 3 0 0 0-4-4l-2 2" fill="none" stroke="#000" stroke-width="2.2" stroke-linecap="round"/></svg></a>
<a class="abs social" style="left:227px" aria-label="Social profile"><svg viewBox="0 0 24 24"><path d="M10 14l4-4M8.5 11.5l-2 2a3 3 0 0 0 4 4l2-2M15.5 12.5l2-2a3 3 0 0 0-4-4l-2 2" fill="none" stroke="#000" stroke-width="2.2" stroke-linecap="round"/></svg></a>
<a class="abs social" style="left:284px" aria-label="Social profile"><svg viewBox="0 0 24 24"><path d="M10 14l4-4M8.5 11.5l-2 2a3 3 0 0 0 4 4l2-2M15.5 12.5l2-2a3 3 0 0 0-4-4l-2 2" fill="none" stroke="#000" stroke-width="2.2" stroke-linecap="round"/></svg></a>

<div class="abs foot-head" style="left:430px">QUICK LINK</div>
<ul class="abs foot-list" style="left:430px">
  <li><svg viewBox="0 0 14 12"><path d="M0 5h8V1l6 5-6 5V7H0z"/></svg>Home</li>
  <li><svg viewBox="0 0 14 12"><path d="M0 5h8V1l6 5-6 5V7H0z"/></svg>About</li>
  <li><svg viewBox="0 0 14 12"><path d="M0 5h8V1l6 5-6 5V7H0z"/></svg>Services</li>
  <li><svg viewBox="0 0 14 12"><path d="M0 5h8V1l6 5-6 5V7H0z"/></svg>Fees and information</li>
  <li><svg viewBox="0 0 14 12"><path d="M0 5h8V1l6 5-6 5V7H0z"/></svg>Contact Us</li>
</ul>

<div class="abs foot-head" style="left:662px">HELP LINKS</div>
<ul class="abs foot-list" style="left:662px">
  <li><svg viewBox="0 0 14 12"><path d="M0 5h8V1l6 5-6 5V7H0z"/></svg>FAQ</li>
  <li><svg viewBox="0 0 14 12"><path d="M0 5h8V1l6 5-6 5V7H0z"/></svg>Terms of use</li>
  <li><svg viewBox="0 0 14 12"><path d="M0 5h8V1l6 5-6 5V7H0z"/></svg>Privacy Policy</li>
  <li><svg viewBox="0 0 14 12"><path d="M0 5h8V1l6 5-6 5V7H0z"/></svg>Support Links</li>
  <li><svg viewBox="0 0 14 12"><path d="M0 5h8V1l6 5-6 5V7H0z"/></svg>Conditions</li>
</ul>

<div class="abs foot-head" style="left:880px">CONTACT US</div>
<div class="abs contact-row" style="top:2505px">
  <span class="ico"><svg viewBox="0 0 24 24"><path d="M12 2a7 7 0 0 0-7 7c0 5 7 13 7 13s7-8 7-13a7 7 0 0 0-7-7zm0 9.5A2.5 2.5 0 1 1 12 6.5a2.5 2.5 0 0 1 0 5z"/></svg></span>
  <span>Dr.Clara Hayes<br>United States</span>
</div>
<div class="abs contact-row" style="top:2574px">
  <span class="ico"><svg viewBox="0 0 24 24"><path d="M6.6 10.8a15.1 15.1 0 0 0 6.6 6.6l2.2-2.2a1 1 0 0 1 1-.25 11.4 11.4 0 0 0 3.6.57 1 1 0 0 1 1 1V20a1 1 0 0 1-1 1A17 17 0 0 1 3 4a1 1 0 0 1 1-1h3.5a1 1 0 0 1 1 1c0 1.250.2 2.450.57 3.570a1 1 0 0 1-.25 1z"/></svg></span>
  <span>+1 555 014 2277</span>
</div>
<div class="abs contact-row" style="top:2626px">
  <span class="ico"><svg viewBox="0 0 24 24"><path d="M2 5h20v14H2V5zm2 2v.4l8 5 8-5V7H4z"/></svg></span>
  <span>info@dr.clarahayes.com</span>
</div>

<div class="abs rule"></div>
<div class="abs copyright">Copyrights@2024.Dr.Clara Hayes.All Rights Reserved</div>

</body>
</html>
```